Business Card Design for Varomir Facility Services

We are looking for a Business Card Design for the Company "Varomir Facility Services."
Front side:
- Company Logo (small)
- Company Name, address, pohone, website and personal data.
- white background, for text e.g. company colors (blue or green like in the logo)
Please use following data:
Company data:
Varomir Facility Services Kostelac
Birkenhaldweg 14
6330 Cham
www.varomir-fs.ch
Person data:
Tarik Kostelac
Geschäftsführer
+41 76 519 47 83
info@varomir-fs.ch
Back side:
could be colored in blue or green
please use a big logo sing and some smaller icons to say what is all beeing offered in facility services, like cleaning, maintenance cleaning
industrial cleaning, caretaking, gardening, disposal. There is no need for everyone of the icons if there are similar or an icon is standing for more of them.
colors to use:
blue: HEX 246BB0
green: HEX 52B33E

```html
<!DOCTYPE html>
<html lang="de">
<head>
<meta charset="utf-8">
<title>Varomir Facility Services – Visitenkarte</title>
<link href="https://fonts.googleapis.com/css2?family=Lato:wght@400;700;900&display=swap" rel="stylesheet">
<style>
  :root {
    --brand-blue: #246BB0;
    --brand-green: #52B33E;
    --paper: #ffffff;
    --backdrop: #e4e4e6;
    --line-soft: rgba(255,255,255,0.28);
  }
  * { box-sizing: border-box; margin: 0; padding: 0; }
  html, body { width: 1200px; height: 900px; overflow: hidden; }
  body {
    background: var(--backdrop);
    font-family: "Lato", Arial, sans-serif;
    position: relative;
  }
  .card {
    position: absolute;
    width: 540px;
    height: 340px;
    border-radius: 26px;
    overflow: hidden;
    box-shadow: 0 10px 28px rgba(0,0,0,0.18);
  }

  /* Back side */
  .card-back {
    left: 40px; top: 280px;
    background: var(--brand-blue);
    color: var(--paper);
  }
  .card-back .top-rule,
  .card-back .bottom-rule {
    position: absolute; left: 0; right: 0; height: 1px; background: var(--line-soft);
  }
  .card-back .top-rule { top: 62px; }
  .card-back .bottom-rule { top: 262px; }
  .back-brand {
    position: absolute; left: 40px; top: 112px;
    display: flex; align-items: center; gap: 12px;
  }
  .brand-dot {
    width: 18px; height: 18px; border-radius: 50%;
    background: var(--paper); flex: none;
  }
  .back-brand .brand-name {
    font-weight: 900; font-size: 22px; letter-spacing: 1.5px; text-transform: uppercase;
    line-height: 1.15; color: var(--paper);
  }
  .service-icon {
    position: absolute; right: 56px; top: 108px;
    width: 52px; height: 52px; border-radius: 50%; background: var(--paper);
    display: flex; align-items: center; justify-content: center;
  }
  .service-list {
    position: absolute; left: 40px; right: 40px; top: 278px;
    font-size: 12.5px; letter-spacing: 1.2px; text-transform: uppercase;
    line-height: 1.6; text-align: center;
  }

  /* Front side */
  .card-front {
    left: 620px; top: 280px;
    background: var(--paper);
  }
  .card-front .wave { position: absolute; inset: 0; }
  .front-brand {
    position: absolute; left: 32px; top: 58px;
    display: flex; align-items: center; gap: 10px;
  }
  .front-brand .brand-dot { background: var(--brand-green); width: 16px; height: 16px; }
  .front-brand .brand-name {
    font-weight: 900; font-size: 20px; letter-spacing: 1.2px; text-transform: uppercase;
    line-height: 1.15; color: var(--brand-blue);
  }
  .contact {
    position: absolute; left: 34px; top: 182px;
    color: var(--paper); font-size: 13px; line-height: 1.32;
  }
  .contact .person-name { font-weight: 900; font-size: 16px; letter-spacing: 0.8px; text-transform: uppercase; }
  .contact .person-role { margin-bottom: 8px; }
  .contact .label { font-weight: 700; }
</style>
</head>
<body>

  <section class="card card-back" aria-label="Rückseite">
    <div class="top-rule"></div>
    <div class="back-brand">
      <span class="brand-dot"></span>
      <span class="brand-name">Varomir<br>Facility Services</span>
    </div>
    <div class="service-icon">
      <svg width="30" height="30" viewBox="0 0 30 30" aria-hidden="true">
        <line x1="22" y1="4" x2="14" y2="16" stroke="#246BB0" stroke-width="2.4" stroke-linecap="round"/>
        <path d="M11 14 L18 19 L13 27 L5 22 Z" fill="#246BB0"/>
      </svg>
    </div>
    <div class="bottom-rule"></div>
    <p class="service-list">
      Cleaning | Maintenance Cleaning | Industrial Cleaning<br>
      Caretaking | Gardening | Disposal
    </p>
  </section>

  <section class="card card-front" aria-label="Vorderseite">
    <svg class="wave" width="540" height="340" viewBox="0 0 540 340" aria-hidden="true">
      <path d="M0 165 C 200 168, 390 150, 540 70 L540 340 L0 340 Z" fill="#246BB0"/>
      <path d="M190 162 C 330 158, 450 120, 540 62" fill="none" stroke="#52B33E" stroke-width="7" stroke-linecap="round"/>
    </svg>
    <div class="front-brand">
      <span class="brand-dot"></span>
      <span class="brand-name">Varomir<br>Facility Services</span>
    </div>
    <div class="contact">
      <p class="person-name">Tarik Kostelac</p>
      <p class="person-role">Geschäftsführer</p>
      <p>Varomir Facility Services Kostelac</p>
      <p>Birkenhaldweg 14 6330 Cham</p>
      <p><span class="label">P:</span> +41 76 519 47 83</p>
      <p><span class="label">E:</span> info@varomir-fs.ch | <span class="label">W:</span> www.varomir-fs.ch</p>
    </div>
  </section>

</body>
</html>
```